Veriplume Digital Badge Header/Banner for Nimbleway People Certificaiton

We need a new page header/banner for Veriplume https://www.badgequill.example/ where we have all our digital badges and certificates for our Nimbleway People Coaching https://www.badgequill.example/issuer/48213/credentials

https://www.badgequill.example/group/503118
https://www.badgequill.example/group/514927
https://www.badgequill.example/group/520364

https://www.brightfernpartners.example/

Target Market(s)

HR Professionals

Font styles to use
Sans Serif

```html
<!DOCTYPE html>
<html lang="en">
<head>
<meta charset="utf-8">
<title>Veriplume — Nimbleway People Digital Badges Header</title>
<link href="https://fonts.googleapis.com/css2?family=Montserrat:wght@400;500;800&display=swap" rel="stylesheet">
<style>
  :root {
    --page-bg: #ffffff;
    --band-blue: #3762c9;
    --band-indigo: #4a4fb8;
    --band-violet: #7a4ac6;
    --texture-tint: rgba(130, 150, 235, 0.18);
    --seal-cyan: rgba(95, 235, 255, 0.75);
    --seal-blue: rgba(80, 150, 240, 0.55);
    --accent-cyan: #00e0ff;
    --text-white: #ffffff;
  }
  * { margin: 0; padding: 0; box-sizing: border-box; }
  html, body {
    width: 1200px;
    height: 511px;
    overflow: hidden;
    background: var(--page-bg);
  }
  .canvas {
    position: relative;
    width: 1200px;
    height: 511px;
  }
  .header-band {
    position: absolute;
    left: 42px;
    top: 85px;
    width: 1116px;
    height: 339px;
    overflow: hidden;
    background:
      radial-gradient(ellipse 420px 220px at 330px 170px, rgba(40, 40, 130, 0.35), transparent 70%),
      linear-gradient(115deg, var(--band-blue) 0%, var(--band-indigo) 45%, var(--band-violet) 100%);
  }
  .band-texture {
    position: absolute;
    inset: 0;
    background:
      radial-gradient(ellipse 520px 120px at 20% 100%, var(--texture-tint), transparent 70%),
      radial-gradient(ellipse 600px 140px at 85% 95%, var(--texture-tint), transparent 70%),
      radial-gradient(ellipse 900px 160px at 50% 0%, rgba(110, 140, 230, 0.14), transparent 70%);
  }
  .headline {
    position: absolute;
    left: 55px;
    top: 56px;
    font-family: "Montserrat", sans-serif;
    color: var(--text-white);
    line-height: 1;
  }
  .headline__lead {
    display: block;
    font-weight: 500;
    font-size: 39px;
    letter-spacing: 0.22em;
    margin-left: 5px;
  }
  .headline__strong {
    display: block;
    font-weight: 800;
    font-size: 56px;
    letter-spacing: 0.005em;
    margin-top: 12px;
  }
  .headline__strong + .headline__strong { margin-top: 8px; }
  .headline__accent { color: var(--accent-cyan); }
  .headline__light { font-weight: 400; }
  .headline__close {
    display: block;
    font-weight: 400;
    font-size: 50px;
    margin-top: 14px;
  }
  .seal-art {
    position: absolute;
    left: 765px;
    top: 20px;
    width: 300px;
    height: 300px;
    border-radius: 50%;
    background: radial-gradient(circle at 50% 50%, var(--seal-blue) 0%, var(--seal-cyan) 70%, rgba(95, 235, 255, 0.2) 88%, transparent 100%);
  }
</style>
</head>
<body>
  <div class="canvas">
    <section class="header-band">
      <div class="band-texture" role="img" aria-label="Faint chain-link and network line texture over the gradient"></div>
      <h1 class="headline">
        <span class="headline__lead">WE HAVE ALL OUR</span>
        <span class="headline__strong"><span class="headline__accent">DIGITAL BADGES</span> AND</span>
        <span class="headline__strong"><span class="headline__accent">CERTIFICATES</span> <span class="headline__light">FOR</span></span>
        <span class="headline__close">OUR NIMBLEWAY PEOPLE</span>
      </h1>
      <div class="seal-art" role="img" aria-label="Glowing cyan certificate seal illustration with a tick"></div>
    </section>
  </div>
</body>
</html>
```